bamboo kettle vietnamese restaurant in need of a new menu

a family owned vietnamese restaurant in need of a new menu design that is fun, classy, and yet simple. menu that will catch the customers eyes. easy to read yet flows nicely. like to use the color green (basil green color) creme yellow and maroon. open to other colors as long as it looks nice together. our restaurant is family oriented, casual yet has a nice ambiance atmosphere.
prefer 11x17 portrait double sided. attached is our menu with the current price updated so use the info on this to start creating! looking for something unique, professional and one of a kind menu!
Updates
please use your own creative layout and design. we are open to ideas. the files uploaded are the updated prices and the logo is to use whichever one you feel goes with the menu.
Reason: don't see anything we like so far...please be creative!
Target Market(s)
restaurant consumers
Industry/Entity Type
Restaurant
Look and feel

```html
<!DOCTYPE html>
<html lang="en">
<head>
<meta charset="utf-8">
<title>Bamboo Kettle — Menu</title>
<link rel="stylesheet" href="https://fonts.googleapis.com/css2?family=League+Gothic&family=Oswald:wght@300;400;500&display=swap">
<style>
:root{
  --basil:#78bf3f;
  --basil-deep:#5fa82d;
  --leaf:#d6ebc3;
  --leaf-soft:#eaf5df;
  --ink:#262626;
  --muted:#9c9c9c;
  --paper:#ffffff;
  --flame:#f06a1d;
}
*{margin:0;padding:0;box-sizing:border-box}
html,body{width:1200px;height:777px;overflow:hidden;background:var(--paper)}
.menu{position:relative;width:1200px;height:777px;overflow:hidden;color:var(--ink);font-family:"Oswald",sans-serif;text-transform:uppercase}
.foliage{position:absolute;inset:0;width:1200px;height:777px;z-index:0}
.abs{position:absolute;z-index:2}
.heading{font-family:"League Gothic",sans-serif;color:var(--basil);font-weight:400;line-height:.85;letter-spacing:1px}
.sub{font-family:"Oswald",sans-serif;font-weight:400;font-size:12px;line-height:1.1;color:var(--ink)}
.note{font-weight:300;font-size:8.2px;line-height:1.25}
.section-head{display:flex;align-items:flex-start;gap:6px}
.section-head .heading{flex:none}
.section-head .caption{padding-top:2px}
.item{display:grid;grid-template-columns:16px 1fr;margin-bottom:5px}
.item .no{font-size:10.5px;font-weight:400;line-height:1.25}
.item h3{font-size:10.5px;font-weight:500;line-height:1.25;letter-spacing:.1px}
.item h3 b,.price{color:var(--basil);font-weight:300;font-size:11px;margin-left:3px}
.item p{font-size:8.3px;font-weight:300;line-height:1.22}
.item p i{font-style:italic}
.item p strong{font-weight:500;font-size:9.5px}
.flame{display:inline-block;width:7px;height:9px;vertical-align:-1px;margin-left:2px}
.extras{position:absolute;left:400px;top:354px;width:400px;height:96px;z-index:1}
.extras ul{position:absolute;left:16px;top:6px;list-style:none;color:#fff;font-size:8.6px;font-weight:500;line-height:1.28}
.extras ul li span{font-weight:300}
.photo{position:absolute;border-radius:50%;z-index:1}
</style>
</head>
<body>
<div class="menu">

  <svg class="foliage" viewBox="0 0 1200 777" role="img" aria-label="Soft green watercolour leaves and herb sprigs scattered behind the menu">
    <defs>
      <radialGradient id="leafwash" cx="50%" cy="50%" r="50%">
        <stop offset="0" stop-color="#cfe7b6" stop-opacity=".6"/>
        <stop offset="1" stop-color="#e9f4de" stop-opacity="0"/>
      </radialGradient>
    </defs>
    <ellipse cx="80" cy="40" rx="120" ry="70" fill="url(#leafwash)"/>
    <ellipse cx="320" cy="40" rx="90" ry="60" fill="url(#leafwash)"/>
    <ellipse cx="60" cy="620" rx="90" ry="150" fill="url(#leafwash)"/>
    <ellipse cx="300" cy="720" rx="110" ry="70" fill="url(#leafwash)"/>
    <ellipse cx="560" cy="620" rx="120" ry="80" fill="url(#leafwash)"/>
    <ellipse cx="880" cy="40" rx="120" ry="70" fill="url(#leafwash)"/>
    <ellipse cx="1130" cy="250" rx="110" ry="140" fill="url(#leafwash)"/>
    <ellipse cx="880" cy="330" rx="110" ry="60" fill="url(#leafwash)"/>
    <ellipse cx="1110" cy="720" rx="130" ry="80" fill="url(#leafwash)"/>
    <ellipse cx="640" cy="330" rx="70" ry="40" fill="url(#leafwash)"/>
  </svg>

  <!-- APPETIZERS -->
  <h1 class="heading abs" style="left:128px;top:22px;font-size:56px">Appetizers</h1>
  <p class="note abs" style="left:29px;top:73px;width:350px">Spring rolls (2) comes with lettuce, vermicelli noodles rolled in rice paper served with peanut sauce with choice of: (cannot be mixed):</p>

  <div class="abs" style="left:40px;top:105px;width:160px">
    <div class="item"><span class="no">1.</span><div><h3>Goi Cuon Tom &amp; Thit Heo <b>4.50</b></h3><p>Shrimp &amp; pork spring rolls</p></div></div>
    <div class="item"><span class="no">2.</span><div><h3>Goi Cuon Thit Heo / Ga / Or Bo Nuong <b>5.50</b></h3><p>Choice of: grilled pork / grilled chicken or grilled beef spring rolls</p></div></div>
    <div class="item"><span class="no">3.</span><div><h3>Bi Cuon <b>4.50</b></h3><p>Pork skin roasted with rice powder spring rolls</p></div></div>
    <div class="item"><span class="no">4.</span><div><h3>Cha Gio (2) <b>4.50</b></h3><p>Fried eggrolls with shrimp, pork &amp; vegetables rolled in egg wrap</p></div></div>
    <div class="item"><span class="no">5.</span><div><h3>Canh Ga Nuoc Mam (6) <b>7.95</b></h3><p>Fried chicken wings</p></div></div>
  </div>

  <div class="abs" style="left:210px;top:105px;width:160px">
    <div class="item"><span class="no">6.</span><div><h3>Gio Tom (4) <b>5.95</b></h3><p>Fried shrimp rolls</p></div></div>
    <div class="item"><span class="no">7.</span><div><h3>Ca Vien Chien (8) <b>4.95</b></h3><p>Fried fish balls</p></div></div>
    <div class="item"><span class="no">8.</span><div><h3>Chao Tom (2) <b>7.95</b></h3><p>Grilled shrimp paste wrapped around sugar cane stick</p></div></div>
    <div class="item"><span class="no">9.</span><div><h3>Wonton Soup <b>(S) 4.95 (L) 7.50</b></h3><p>Wonton shrimp &amp; pork soup</p></div></div>
    <div class="item"><span class="no">10.</span><div><h3>Tom Cua Soup <b>(S) 4.95 (L) 7.50</b></h3><p>Crab meat, shrimp &amp; egg soup</p></div></div>
  </div>

  <p class="note abs" style="left:29px;top:308px;width:350px">Vietnamese salad comes with thin cabbage, carrots, onions, mints, crushed peanuts tossed in lime juice &amp; vinegar with the following choices of:</p>

  <div class="abs" style="left:40px;top:334px;width:160px">
    <div class="item"><span class="no">11.</span><div><h3>Goi Ga <b>8.95</b></h3><p>Chicken salad</p></div></div>
    <div class="item"><span class="no">12.</span><div><h3>Goi Tom <b>9.95</b></h3><p>Shrimp salad</p></div></div>
  </div>
  <div class="abs" style="left:210px;top:337px;width:160px">
    <div class="item"><span class="no">13.</span><div><h3>Bo Tai Chanh <b>11.95</b></h3><p>Rare thin sliced beef with onions, mints, basils, crushed peanuts in lime juice &amp; vinegar</p></div></div>
    <div class="item"><span class="no">14.</span><div><h3>Chim Cut Roti <b>11.95</b></h3><p>Roasted quails served with salt &amp; pepper</p></div></div>
  </div>

  <!-- HU TIEU -->
  <h1 class="heading abs" style="left:29px;top:412px;font-size:54px">Hu Tieu (Mi)</h1>
  <p class="sub abs" style="left:30px;top:455px">Noodle Soup</p>
  <p class="note abs" style="left:30px;top:469px">Rice or egg noodle soup in pork broth</p>

  <div class="abs" style="left:40px;top:484px;width:325px">
    <div class="item"><span class="no">15.</span><div><h3>Hu Tieu (Mi) Dac Biet <b>10.50</b></h3><p>Choice of: rice or egg noodle with shrimp, roast pork, chicken, imitation crab, quail eggs, ground pork &amp; fried shrimp cracker combination noodle soup</p></div></div>
    <div class="item"><span class="no">16.</span><div><h3>Hu Tieu (Mi) Hai San <b>11.50</b></h3><p>Choice of: rice or egg noodle with shrimp, scallop, squid, fish balls &amp; imitation crab noodle soup</p></div></div>
    <div class="item"><span class="no">17.</span><div><h3>Hu Tieu Mytho <b>9.95</b></h3><p>Shrimp, roast pork, chicken, fish ball, imitation crab &amp; ground pork with clear noodle soup</p></div></div>
    <div class="item"><span class="no">18.</span><div><h3>Hu Tieu Sate <b>9.50</b><svg class="flame" viewBox="0 0 10 13"><path d="M5 0C6 4 10 5 10 8.5A5 4.5 0 0 1 0 8.5C0 6 2 5 2.5 3 3.5 4.5 4 5 4.5 5.5 5.5 3.5 5 1.5 5 0Z" fill="var(--flame)"/></svg></h3><p>Beef with tomato slices, cucumber, bean sprouts &amp; crushed peanuts in spicy noodle soup</p></div></div>
  </div>

  <div class="abs" style="left:40px;top:650px;width:160px">
    <div class="item"><span class="no">19.</span><div><h3>Hu Tieu (Mi) Kho Dac Biet <b>10.95</b></h3><p>Choice of: rice or egg noodle with shrimp, roast pork, chicken, imitation crab, ground pork and fried shrimp cracker with soup on the side</p></div></div>
    <div class="item"><span class="no">20.</span><div><h3>Mi Hoanh Thanh <b>8.95</b></h3><p>Wonton with egg noodle soup<br><strong>+Xa Xiu (roast pork)</strong> <span class="price">10.95</span></p></div></div>
  </div>
  <div class="abs" style="left:212px;top:650px;width:160px">
    <div class="item"><span class="no">21.</span><div><h3>Banh Canh Tom Thit Gio Heo <b>9.50</b></h3><p>Shrimp, pork knuckle &amp; vietnamese big noodle soup</p></div></div>
    <div class="item"><span class="no">22.</span><div><h3>Banh Canh Ga <b>8.95</b></h3><p>Chicken with vietnamese big noodle soup</p></div></div>
  </div>

  <!-- PHO -->
  <h1 class="heading abs" style="left:578px;top:22px;font-size:56px">Pho</h1>
  <p class="sub abs" style="left:551px;top:68px;font-size:13px">Rice Noodles Soup</p>

  <div class="abs" style="left:438px;top:106px;width:165px">
    <div class="item"><span class="no">23.</span><div><h3>Pho Dac Biet <b>9.50</b></h3><p>Steak, brisket, flank, tendon, tripe &amp; meatballs combination noodle soup</p></div></div>
    <div class="item"><span class="no">24.</span><div><h3>Pho <b>8.50</b></h3><p>Noodle soup with choices up to 3 items: <i>steak, brisket, flank, tendon, tripe, meatball or vegetables</i></p></div></div>
    <div class="item"><span class="no">25.</span><div><h3>Pho Ga Vietnam (Ga Di Bo) <b>10.50</b></h3><p>Free range chicken noodle soup</p></div></div>
    <div class="item"><span class="no">26.</span><div><h3>Pho Ga My <b>9.50</b></h3><p>White chicken &amp; mixed vegetables noodle soup</p></div></div>
    <div class="item"><span class="no">27.</span><div><h3>Pho Thit Heo / Bo / Or Ga Nuong <b>10.50</b></h3><p>Choice of: grilled pork, grilled beef or grilled chicken with mixed vegetables noodle soup</p></div></div>
  </div>
  <div class="abs" style="left:610px;top:106px;width:175px">
    <div class="item"><span class="no">28.</span><div><h3>Pho Do Bien <b>11.50</b></h3><p>Shrimp, scallop, squid, fish balls, imitation crab &amp; vegetables seafood noodle soup</p></div></div>
    <div class="item"><span class="no">29.</span><div><h3>Pho Tom <b>9.75</b></h3><p>Shrimp with mixed vegetables noodle soup</p></div></div>
    <div class="item"><span class="no">30.</span><div><h3>Pho Do Bien Chua Cay <b>11.50</b><svg class="flame" viewBox="0 0 10 13"><path d="M5 0C6 4 10 5 10 8.5A5 4.5 0 0 1 0 8.5C0 6 2 5 2.5 3 3.5 4.5 4 5 4.5 5.5 5.5 3.5 5 1.5 5 0Z" fill="var(--flame)"/></svg></h3><p>Shrimp, scallop, squid, fish balls &amp; imitation crab in hot &amp; sour seafood noodle soup</p></div></div>
    <div class="item"><span class="no">31.</span><div><h3>Pho Tre Em <b>7.25</b></h3><p>Kid's steak &amp; meatball noodle soup</p></div></div>
  </div>

  <!-- EXTRAS BAND -->
  <div class="extras">
    <svg width="400" height="96" viewBox="0 0 400 96" style="position:absolute;left:0;top:0">
      <rect x="0" y="0" width="250" height="96" fill="var(--basil)"/>
      <rect x="250" y="0" width="148" height="18" fill="var(--basil)"/>
      <rect x="250" y="24" width="140" height="14" fill="var(--basil)"/>
      <rect x="250" y="58" width="145" height="14" fill="var(--basil)"/>
      <rect x="250" y="78" width="130" height="10" fill="var(--basil)"/>
    </svg>
    <ul>
      <li>• X-Large <span>2.00 more</span></li>
      <li>• Extra Meat <span>(steak, chicken, etc.) 3.50</span></li>
      <li>• Extra Shrimp <span>3.00</span></li>
      <li>• Extra Herbs or Vegetables <span>1.50</span></li>
      <li><span>&nbsp;&nbsp;(ex: cilantros, basils, beansprouts, etc.)</span></li>
      <li>• Extra Rice, Soup or Noodles <span>1.50</span></li>
      <li>• Change Noodle or Brown Rice <span>2.00</span></li>
      <li>• Add Fried Egg <span>1.50</span></li>
    </ul>
  </div>
  <div class="photo" role="img" aria-label="Photo of a bowl of pho with sliced beef and noodles" style="left:588px;top:352px;width:116px;height:116px;background:radial-gradient(circle,#c9a266 0%,#b58a4e 45%,#e7e2d6 62%,#f7f5f0 80%);box-shadow:0 2px 6px rgba(0,0,0,.15)"></div>

  <!-- BUN -->
  <div class="section-head abs" style="left:413px;top:474px;width:390px">
    <h1 class="heading" style="font-size:48px">Bun</h1>
    <div class="caption">
      <p class="sub" style="font-size:12.5px">Vermicelli Noodle Bowl</p>
      <p class="note" style="font-size:8.4px;margin-top:2px">All vermicelli bowl comes with fresh lettuce, bean sprouts, sliced cucumbers, shredded carrots &amp; crushed peanuts</p>
    </div>
  </div>

  <div class="abs" style="left:438px;top:534px;width:165px">
    <div class="item"><span class="no">32.</span><div><h3>Bun Dac Biet <b>12.95</b></h3><p>Choice of: grilled pork, grilled chicken or grilled beef with grilled shrimp &amp; fried eggroll special combination vermicelli bowl</p></div></div>
    <div class="item"><span class="no">33.</span><div><h3>Bun - Vermicelli Bowl <b>9.50</b></h3><p>Choice of: grilled pork, grilled chicken or grilled beef<br><strong>+ Eggroll</strong> <span class="price">9.50</span><br><strong>+ Shrimp</strong> <span class="price">10.50</span></p></div></div>
    <div class="item"><span class="no">34.</span><div><h3>Bun Tom Nuong (8) <b>10.50</b></h3><p>Grilled shrimp<br>vermicelli bowl</p></div></div>
  </div>
  <div class="abs" style="left:610px;top:534px;width:160px">
    <div class="item"><span class="no">35.</span><div><h3>Bun Cha Gio (3) <b>9.50</b></h3><p>Fried eggroll vermicelli bowl</p></div></div>
    <div class="item"><span class="no">36.</span><div><h3>Bun Chao Tom (2) <b>9.50</b></h3><p>Grilled shrimp paste vermicelli bowl</p></div></div>
    <div class="item"><span class="no">37.</span><div><h3>Bun Bo Hue <b>9.50</b><svg class="flame" viewBox="0 0 10 13"><path d="M5 0C6 4 10 5 10 8.5A5 4.5 0 0 1 0 8.5C0 6 2 5 2.5 3 3.5 4.5 4 5 4.5 5.5 5.5 3.5 5 1.5 5 0Z" fill="var(--flame)"/></svg></h3><p>Spicy beef noodle soup with beef shank, pork knuckle, pork blood with large vermicelli noodles</p></div></div>
    <div class="item"><span class="no">38.</span><div><h3>Bun Rieu <b>9.50</b></h3><p>Mixed ground pork &amp; crab, pork blood, dried tofu with vermicelli rice noodle in tomato broth soup</p></div></div>
    <div class="item"><span class="no">39.</span><div><h3>Bun Mang Vit <b>9.50</b></h3><p>Duck &amp; bamboo vermicelli noodle soup</p></div></div>
  </div>

  <!-- COM TAM -->
  <h1 class="heading abs" style="left:944px;top:22px;font-size:56px">Com Tam</h1>
  <p class="sub abs" style="left:951px;top:68px;font-size:13px">Broken Rice Plate</p>

  <div class="abs" style="left:836px;top:97px;width:325px">
    <div class="item"><span class="no">40.</span><div><h3>Com Dac Biet <b>14.95</b></h3><p>Special rice combination with grilled chicken, grilled pork, grilled shrimp &amp; fried eggroll</p></div></div>
    <div class="item"><span class="no">41.</span><div><h3>Com Suon Nuong Xa <b>9.95</b></h3><p>Grilled pork chops marinated in lemongrass</p></div></div>
    <div class="item"><span class="no">42.</span><div><h3>Com Suon Bi Cha <b>9.50</b></h3><p>Grilled pork chop, pork skin roasted with rice powder &amp; eggcake</p></div></div>
    <div class="item"><span class="no">43.</span><div><h3>Com Thit Nuong, Ga Nuong or Bo Nuong <b>9.75</b></h3><p>Choice of: grilled pork, grilled chicken or grilled beef<br><strong>+Shrimp</strong> <span class="price">10.95</span></p></div></div>
    <div class="item"><span class="no">44.</span><div><h3>Com Suon Dai Han <b>13.95</b></h3><p>Grilled korean bbq ribs</p></div></div>
  </div>
  <div class="photo" role="img" aria-label="Photo of a broken rice plate with grilled pork chop, egg cake and pickled vegetables" style="left:1056px;top:210px;width:150px;height:150px;background:radial-gradient(circle at 45% 55%,#8a4a2a 0%,#b9773e 25%,#e6c77a 42%,#f3eee2 60%,#fbfaf6 78%);box-shadow:0 2px 8px rgba(0,0,0,.15)"></div>

  <!-- COM CHIEN -->
  <div class="section-head abs" style="left:810px;top:320px;width:245px">
    <h1 class="heading" style="font-size:48px">Com Chien</h1>
    <div class="caption">
      <p class="sub" style="font-size:12.5px">Fried Rice</p>
      <p class="note" style="color:var(--muted);margin-top:2px">Fried rice is cooked with egg, peas &amp; carrots</p>
    </div>
  </div>

  <div class="abs" style="left:836px;top:373px;width:165px">
    <div class="item"><span class="no">45.</span><div><h3>Com Chien Thap Cam <b>10.95</b></h3><p>House special fried rice with shrimp, roasted pork, sausage with peas &amp; carrots</p></div></div>
    <div class="item"><span class="no">46.</span><div><h3>Com Chien Tom <b>9.95</b></h3><p>Shrimp fried rice</p></div></div>
    <div class="item"><span class="no">47.</span><div><h3>Com Chien Ga <b>9.95</b></h3><p>Chicken fried rice</p></div></div>
  </div>
  <div class="abs" style="left:1006px;top:373px;width:170px">
    <div class="item"><span class="no">48.</span><div><h3>Com Chien Canh Ga <b>9.50</b></h3><p>Fried rice with fried chicken wings</p></div></div>
    <div class="item"><span class="no">49.</span><div><h3>Com Chien Bo Luc Lac <b>9.50</b></h3><p>Shaking beef stir fry filet mignon with bell peppers with fried rice<br><strong>+ Shrimp</strong> <span class="price">16.95</span></p></div></div>
  </div>

  <!-- XAO -->
  <div class="section-head abs" style="left:810px;top:496px;width:200px">
    <h1 class="heading" style="font-size:48px">Xao</h1>
    <p class="sub caption" style="font-size:12.5px;line-height:1.05">Stir Fry<br>With Rice<br>Plate</p>
  </div>

  <div class="abs" style="left:836px;top:548px;width:165px">
    <div class="item"><span class="no">50.</span><div><h3>Ga Xao Gung <b>9.95</b></h3><p>Stir fry chicken with ginger</p></div></div>
    <div class="item"><span class="no">51.</span><div><h3>Ga or Bo Xao Xa Ot <b>9.95</b><svg class="flame" viewBox="0 0 10 13"><path d="M5 0C6 4 10 5 10 8.5A5 4.5 0 0 1 0 8.5C0 6 2 5 2.5 3 3.5 4.5 4 5 4.5 5.5 5.5 3.5 5 1.5 5 0Z" fill="var(--flame)"/></svg></h3><p>Choice of: stir fry chicken or beef in hot chili &amp; lemongrass</p></div></div>
    <div class="item"><span class="no">52.</span><div><h3>Tom Xao Xa Ot <b>10.95</b><svg class="flame" viewBox="0 0 10 13"><path d="M5 0C6 4 10 5 10 8.5A5 4.5 0 0 1 0 8.5C0 6 2 5 2.5 3 3.5 4.5 4 5 4.5 5.5 5.5 3.5 5 1.5 5 0Z" fill="var(--flame)"/></svg></h3><p>Stir fry shrimp in hot chilli &amp; lemongrass</p></div></div>
    <div class="item"><span class="no">53.</span><div><h3>Ga or Bo Xao Rau Cai <b>9.95</b></h3><p>Choice of: stir fry chicken or beef with mixed vegetables</p></div></div>
    <div class="item"><span class="no">54.</span><div><h3>Tom Xao Rau Cai <b>10.95</b></h3><p>Stir fry shrimp with mixed vegetables</p></div></div>
  </div>
  <div class="abs" style="left:1006px;top:548px;width:170px">
    <div class="item"><span class="no">55.</span><div><h3>Mi Xao Mem or Don Hai San <b>14.95</b></h3><p>Choice of: soft or crispy noodles stir fry with shrimp, squid, fish ball &amp; imitation crab with vegetables</p></div></div>
    <div class="item"><span class="no">56.</span><div><h3>Com Tom Rang Chay Mo <b>10.95</b></h3><p>Stir fry shrimp, ginger, onion &amp; bell pepper in garlic sauce</p></div></div>
    <div class="item"><span class="no">57.</span><div><h3>Canh Chua Ca or Tom <b>10.95</b></h3><p>Choice of: fish or shrimp soup with tomato, pineapple, okra &amp; bean sprouts served with white rice (serving 2-4)</p></div></div>
    <div class="item"><span class="no">58.</span><div><h3>Ca Kho To <b>10.95</b></h3><p>Braised swai fish in clay pot with black pepper &amp; dry shallots served with white rice</p></div></div>
  </div>

</div>
</body>
</html>
```